Business Card - high end, modern health care

Hey designers!

We need a double sided business card for the boutique, cutting edge physical therapy rehabilitation centre in Sydney's Northern Beaches.

With the most qualified physios in the area The Harbourview Motion Clinic does what other physiotherapy practices do not, we take our time with our patients giving them longer appointments, better physios and therefor faster results!

We guarantee that the service people receive at THMC will be unparalleled.

Hence we need a business card to reflect our modern, boutique, high end service. The final design needs to reflect that we are in a class of our own yet with the feel of beachside retreat.

Below I have attached our logo in both blue on white and white on blue. The exact colour is;
and the font that we have used in our logo is Tex Gyre Aventador.

I like the idea of the blue as the main colour as it is more eye catching and our signage onto the main road will be in this blue and in the interest of consistency across marketing the blue needs to be a part of the design. However I would appreciate a few designs onto a wooden background as this is a visual theme within the fitout of the practice.

The design needs to be of standard size (91x55mm).

Target Market(s)

We target people who have an end outcome in mind and those who have had poor experiences with other providers and ensure that everyone gets the care that they deserve with a premium service that is tailored to the individuals circumstances. As a premium service, the target market is highly educated, business and tech savvy with the additional target market of elderly people who have self funded their retirement and see value in paying for the best ongoing rehabilitation to maintain independence.

Industry/Entity Type

Physical Therapy

Contact Information for Business Card

Name, designation( Titled Musculoskeletal Physiotherapist... there will also be those in the company that have multiple designations ie 5 or 6 words long), phone number, email, facebook, instagram, address

Font styles to use
Sans Serif

Colors

Designer to choose colors to be used in the design.

Requirements
Must have
• Front - The logo as large as possible, blue or wooden theme, and all of the important details.
• Back - A blank space/lines on which to write appointment times (no "Appointment, date, time" etc.)
Nice to have
• facebook url
• logos for facebook and instagram
• Mini logos for the phone and email?

```html
<!DOCTYPE html>
<html lang="en">
<head>
<meta charset="utf-8">
<title>The Harbourview Motion Clinic – Business Card</title>
<link rel="stylesheet" href="https://fonts.googleapis.com/css2?family=Raleway:wght@400;500;600;700&display=swap">
<style>
  :root {
    --backdrop: #4c4b7a;
    --brand-blue: #0d58a8;
    --brand-blue-deep: #0b4f98;
    --paper: #ffffff;
    --mark-tint: #e4e8f4;
    --ink-light: #ffffff;
    --rule: rgba(255,255,255,0.75);
    --dash: #6f9fd8;
    --social-dot: #d6e6f7;
  }
  * { box-sizing: border-box; margin: 0; padding: 0; }
  html, body {
    width: 1200px; height: 1000px; overflow: hidden;
    background: var(--backdrop);
    font-family: "Raleway", "Helvetica Neue", Arial, sans-serif;
  }
  .stage { position: relative; width: 1200px; height: 1000px; }

  .card { position: absolute; overflow: hidden; }

  /* Front: white card */
  .card--front {
    left: 136px; top: 78px; width: 660px; height: 377px;
    background: var(--paper);
  }
  .front-watermark {
    position: absolute; left: 331px; top: 42px;
    width: 297px; height: 297px; border-radius: 50%;
    background: var(--mark-tint);
  }
  .front-brand {
    position: absolute; left: 40px; top: 42px;
    display: flex; align-items: center; gap: 8px;
    color: var(--brand-blue); font-weight: 700;
  }
  .front-brand__dot {
    width: 56px; height: 56px; border-radius: 50%;
    background: var(--brand-blue); flex: none;
  }
  .front-brand__name { line-height: 1; }
  .front-brand__line1 { display: block; font-size: 27px; letter-spacing: 0.2px; }
  .front-brand__line2 { display: block; font-size: 18px; font-weight: 600; letter-spacing: 7.2px; margin-top: 4px; }

  /* Back: blue card */
  .card--back {
    left: 400px; top: 535px; width: 657px; height: 375px;
    background: var(--brand-blue-deep);
    color: var(--ink-light);
  }
  .person { position: absolute; left: 48px; top: 72px; }
  .person__name { font-size: 25px; font-weight: 400; letter-spacing: 0.2px; }
  .person__role { font-size: 14px; font-weight: 400; margin-top: 7px; }

  .contacts { position: absolute; left: 46px; top: 166px; list-style: none; }
  .contacts li {
    display: flex; align-items: center; gap: 15px;
    font-size: 16.5px; font-weight: 400; height: 24px;
  }
  .contacts li + li { margin-top: 8px; }
  .contacts .social { font-size: 15px; }
  .contacts .social--first { margin-top: 18px; }
  .contacts svg { flex: none; }
  .social-dot {
    width: 25px; height: 25px; border-radius: 50%;
    background: var(--social-dot); border: 2px solid var(--ink-light); flex: none;
  }

  .divider {
    position: absolute; left: 340px; top: 77px;
    width: 1px; height: 218px; background: var(--rule);
  }

  .back-brand {
    position: absolute; left: 371px; top: 78px; width: 240px;
    text-align: center; font-weight: 700; color: var(--ink-light);
  }
  .back-brand__dot {
    width: 168px; height: 168px; border-radius: 50%;
    background: var(--ink-light); margin: 0 auto;
  }
  .back-brand__line1 { display: block; font-size: 19px; margin-top: 16px; letter-spacing: 0.1px; }
  .back-brand__line2 { display: block; font-size: 12.5px; font-weight: 600; letter-spacing: 4.6px; margin-top: 1px; }

  .appointment-line {
    position: absolute; left: 48px; top: 348px; width: 570px;
    border-top: 1px dashed var(--dash);
  }
</style>
</head>
<body>
<main class="stage">

  <section class="card card--front" aria-label="Business card front">
    <div class="front-watermark" aria-hidden="true"></div>
    <div class="front-brand">
      <span class="front-brand__dot" aria-hidden="true"></span>
      <span class="front-brand__name">
        <span class="front-brand__line1">THE HARBOURVIEW</span>
        <span class="front-brand__line2">MOTION CLINIC</span>
      </span>
    </div>
  </section>

  <section class="card card--back" aria-label="Business card back">
    <div class="person">
      <p class="person__name">Name of Person</p>
      <p class="person__role">Designation</p>
    </div>

    <ul class="contacts">
      <li>
        <svg width="25" height="25" viewBox="0 0 25 25" aria-hidden="true">
          <circle cx="12.5" cy="12.5" r="11" fill="none" stroke="#fff" stroke-width="1.6"/>
          <path d="M9 7.2c.6-.5 1.3-.4 1.6.2l1 1.8c.3.5.1 1-.3 1.3l-.7.5c.5 1.3 1.4 2.3 2.6 3l.6-.6c.4-.4 1-.5 1.4-.2l1.7 1.1c.6.4.6 1.1.1 1.6l-.8.8c-.6.6-1.5.7-2.3.3-2.600-1.3-4.5-3.5-5.5-6.2-.3-.8-.1-1.7.5-2.3z" fill="#fff"/>
        </svg>
        <span>555.014.2290</span>
      </li>
      <li>
        <svg width="25" height="25" viewBox="0 0 25 25" aria-hidden="true">
          <rect x="1.5" y="5.5" width="22" height="14" fill="none" stroke="#fff" stroke-width="1.5"/>
          <path d="M1.5 5.5l11 8 11-8M1.5 19.5l8-7M23.5 19.5l-8-7" fill="none" stroke="#fff" stroke-width="1.3"/>
        </svg>
        <span>hello@harbourviewmotion.com</span>
      </li>
      <li class="social social--first">
        <span class="social-dot" aria-hidden="true"></span>
        <span>profile/name</span>
      </li>
      <li class="social">
        <span class="social-dot" aria-hidden="true"></span>
        <span>gallery_name</span>
      </li>
    </ul>

    <div class="divider" aria-hidden="true"></div>

    <div class="back-brand">
      <div class="back-brand__dot" aria-hidden="true"></div>
      <span class="back-brand__line1">THE HARBOURVIEW</span>
      <span class="back-brand__line2">MOTION CLINIC</span>
    </div>

    <div class="appointment-line" aria-hidden="true"></div>
  </section>

</main>
</body>
</html>
```